New business card for a regional office of a US M&A company

We need business card for a finance company, office based in Hong Kong , our Head office is in US, our business is to Merge and acquires companies , the new office will be a regional office for the Asia Pacific region. We want to use the head office logo as attached ( but don't have to be exactly the same, can be a variation to it) as a base and then add Asia Pacific alongside the logo.
We would prefer to have be bilingual Eng + Chinese, although we don't really have Chinese company name .

Industry/Entity Type

Business

Contact Information for Business Card

Clara Jo Tsang
 

VP,
APAC M&A Operations
Eli Global Asia Pacific Limited
 
Unit 1407, K18
18 Tai Lok Shan Road, 
Hong Kong 
 
M: +852 6038 1742
T : +852 2836 4100
F : +852 2836 4177
VOIP: 4158
 
cjtsang@orinvantage.com

Font styles to use
Serif
Sans Serif

Colors

Designer to choose colors to be used in the design.

Requirements
Must have
• APAC Office

```html
<!DOCTYPE html>
<html lang="en">
<head>
<meta charset="utf-8">
<title>Orin Vantage Asia Pacific – Business Card</title>
<link href="https://fonts.googleapis.com/css2?family=Open+Sans:wght@400;700&display=swap" rel="stylesheet">
<style>
  :root {
    --stage: #3b3532;
    --card: #0d0d0d;
    --card-edge: #1c1c1c;
    --ink: #f2f2f2;
    --ink-soft: #cfcfcf;
    --silver: #a9a9a9;
    --rule: #2e2e2e;
  }
  * { margin: 0; padding: 0; box-sizing: border-box; }
  html, body {
    width: 1200px; height: 900px; overflow: hidden;
    background: var(--stage);
    font-family: "Open Sans", Arial, sans-serif;
  }
  .stage {
    position: relative; width: 1200px; height: 900px;
    display: flex; align-items: center; justify-content: center; gap: 40px;
  }
  .card {
    width: 540px; height: 309px;
    background: var(--card);
    border: 1px solid var(--card-edge);
    position: relative;
    overflow: hidden;
  }
  /* front */
  .card-front { display: flex; }
  .brand-panel {
    width: 46%;
    display: flex; flex-direction: column; align-items: center; justify-content: center;
    gap: 16px;
    border-right: 1px solid var(--rule);
  }
  .brand-square { width: 92px; height: 92px; background: var(--ink); }
  .brand-name {
    color: var(--ink); font-weight: 700; font-size: 13px;
    letter-spacing: 0.08em; text-transform: uppercase;
  }
  .contact-panel {
    flex: 1; padding: 34px 24px 0 26px; color: var(--ink);
  }
  .person-name { font-size: 17px; font-weight: 700; line-height: 1.2; }
  .person-role { font-size: 11.5px; color: var(--ink-soft); margin-top: 2px; }
  .company { font-size: 13px; font-weight: 700; margin-top: 16px; }
  .address { font-size: 12.5px; line-height: 1.45; margin-top: 2px; }
  .lines { list-style: none; margin-top: 16px; font-size: 12.5px; }
  .lines li { display: flex; align-items: center; gap: 10px; line-height: 1.5; }
  .lines svg { width: 10px; height: 10px; fill: var(--ink); flex: none; }
  .lines .plain { padding-left: 0; }
  /* back */
  .card-back {
    display: flex; align-items: center; justify-content: center; gap: 22px;
  }
  .back-square { width: 70px; height: 70px; background: var(--silver); }
  .back-name { color: var(--silver); font-weight: 700; line-height: 1.05; text-transform: uppercase; }
  .back-name .line-1 { font-size: 30px; display: block; }
  .back-name .line-2 { font-size: 21px; display: block; }
</style>
</head>
<body>
<main class="stage">
  <section class="card card-front">
    <div class="brand-panel">
      <div class="brand-square"></div>
      <span class="brand-name">Orin Vantage</span>
    </div>
    <div class="contact-panel">
      <p class="person-name">Clara Jo Tsang VP,</p>
      <p class="person-role">APAC M&amp;A Operations</p>
      <p class="company">Orin Vantage Asia Pacific Ltd</p>
      <p class="address">Unit 1407, K18 18 Tai Lok Shan<br>Road, Hong Kong</p>
      <ul class="lines">
        <li><svg viewBox="0 0 10 10"><rect x="2" y="0" width="6" height="10" rx="1"/></svg>+852 6038 1742</li>
        <li><svg viewBox="0 0 10 10"><path d="M1 1h3l1 2.5-1.5 1a6 6 0 0 0 3 3l1-1.5L10 7v2a1 1 0 0 1-1 1C4 10 0 6 0 1a1 1 0 0 1 1 0z"/></svg>+852 2836 4100</li>
        <li><svg viewBox="0 0 10 10"><rect x="2" y="0" width="6" height="3"/><rect x="0" y="3" width="10" height="5" rx="1"/><rect x="2" y="7" width="6" height="3"/></svg>+852 2836 4177</li>
        <li><svg viewBox="0 0 10 10"><path d="M0 2h10v6H0z M0 2l5 3.5L10 2" fill="var(--ink)"/><path d="M0.6 2.4 5 5.5 9.4 2.4" stroke="var(--card)" stroke-width="0.9" fill="none"/></svg>cjtsang@orinvantage.com</li>
        <li class="plain">VOIP: 4158</li>
      </ul>
    </div>
  </section>

  <section class="card card-back">
    <div class="back-square"></div>
    <p class="back-name"><span class="line-1">Orin Vantage</span><span class="line-2">Asia Pacific Ltd</span></p>
  </section>
</main>
</body>
</html>
```